Goodlooking website for a company who is working in the IT consultancy

We want a new website designed in WordPress. You can take www.vantoro.nl as an example. It should be a website with some short blocks of information about the company, nice pictures of our partners and our employees. A job page with a clear filter.

Target Market(s)

B2B

Industry/Entity Type

It Company

Coding

Coded - Design and coding required

Number of Pages Required

5+ page

Font styles to use
Sans Serif

Colors
0455a3
34a7d8

Requirements
Must have
• Check briefing

```html
<!DOCTYPE html>
<html lang="en">
<head>
<meta charset="utf-8">
<title>Nexol — Critical IT Systems</title>
<link href="https://fonts.googleapis.com/css2?family=Lato:wght@400;700;900&display=swap" rel="stylesheet">
<style>
:root{
  --teal:#17a589;
  --blue:#1d8fc0;
  --navy:#1b2d3a;
  --ink:#222;
  --text:#444;
  --light:#f3f3f3;
  --footer:#ebebeb;
  --white:#fff;
}
*{box-sizing:border-box;margin:0;padding:0}
html,body{width:1200px;height:2922px;overflow:hidden}
body{position:relative;font-family:'Lato',sans-serif;color:var(--text);background:var(--white)}
.abs{position:absolute}
.brand{display:flex;align-items:center;gap:14px}
.brand-dot{width:58px;height:58px;border-radius:50%;background:var(--navy)}
.brand-name{font-size:42px;font-weight:700;letter-spacing:3px;color:var(--navy)}
/* header */
.site-header{left:0;top:0;width:1200px;height:105px;background:var(--white)}
.site-header .brand{position:absolute;left:74px;top:23px}
.main-nav{position:absolute;left:413px;top:38px;display:flex;gap:0;font-size:15px;font-weight:700;color:var(--ink)}
.main-nav a{color:inherit;text-decoration:none;padding:11px 0;line-height:18px}
.main-nav .active{background:linear-gradient(90deg,var(--blue),#176f93);color:#fff;width:97px;text-align:center}
/* hero */
.hero{left:0;top:105px;width:1200px;height:544px;background:linear-gradient(180deg,#3a4654 0%,#5a5448 45%,#7b5a2f 80%,#3a3430 100%)}
.hero h1{position:absolute;left:0;right:0;top:218px;text-align:center;color:#fff;font-size:44px;font-weight:700;line-height:50px}
.hero-dots{position:absolute;left:560px;top:498px;display:flex;gap:9px}
.hero-dots span{width:13px;height:13px;border-radius:50%;background:#fff}
.hero-dots span:first-child{background:var(--blue);border:2px solid #fff}
/* about */
.about-photo{left:74px;top:695px;width:330px;height:330px;border-radius:50%;background:radial-gradient(circle at 55% 60%,#f0c84a 0%,#3d6fb0 35%,#10224a 75%)}
.section-title{font-size:25px;font-weight:900;color:var(--ink);text-transform:uppercase;line-height:30px}
.section-title em{font-style:normal;color:var(--teal)}
.about-text{left:497px;top:715px;width:630px}
.about-text .sub{display:block;color:var(--teal)}
.about-text p{margin-top:16px;font-size:14px;line-height:28px;color:var(--text)}
.btn{display:inline-block;color:#fff;font-weight:700;text-transform:uppercase;text-align:center}
.btn-grad{background:linear-gradient(90deg,var(--blue),var(--navy))}
.about-text .btn{margin-top:26px;width:180px;height:48px;line-height:48px;font-size:14px}
/* services */
.services-band{left:0;top:1077px;width:1200px;height:335px;background:linear-gradient(180deg,#1e2a33,#0f171d)}
.services-title{left:0;top:1120px;width:1200px;text-align:center;color:#fff;font-size:25px;font-weight:900}
.card{top:1180px;width:243px;height:302px;color:#fff;text-align:center;padding:30px 18px 0;box-shadow:0 6px 14px rgba(0,0,0,.2)}
.card svg{width:68px;height:68px}
.card h3{margin-top:18px;font-size:18px;font-weight:700;line-height:24px;text-transform:uppercase}
.card p{margin-top:12px;font-size:13.5px;line-height:25px}
.c1{left:74px;background:linear-gradient(160deg,#1d93c4,#1b5f7e)}
.c2{left:345px;background:linear-gradient(160deg,#1a9f86,#167566)}
.c3{left:615px;background:linear-gradient(160deg,#223744,#182630)}
.c4{left:884px;background:linear-gradient(160deg,#22b39a,#169181)}
/* jobs */
.jobs-title{left:74px;top:1555px}
.job{top:1613px;width:330px}
.job-mark{width:80px;height:72px;background:#d9dde0}
.job h4{margin-top:34px;font-size:20px;font-weight:700;color:#1a7fa8}
.job p{margin-top:8px;font-size:13.5px;line-height:24px;color:var(--text)}
.job .btn{margin-top:16px;width:97px;height:32px;line-height:32px;font-size:11px;background:var(--navy)}
.job-a{left:74px}.job-b{left:432px}
.jobs-photo{left:797px;top:1562px;width:330px;height:330px;border-radius:50%;background:linear-gradient(160deg,#e8eef3,#b8c7d3 50%,#3b4a5c)}
/* contact */
.contact{left:0;top:1946px;width:1200px;height:442px;background:var(--light)}
.contact-photo{left:0;top:1946px;width:480px;height:442px;background:linear-gradient(90deg,#2a3550 0%,#4c5c78 50%,rgba(243,243,243,1) 100%)}
.contact-title{left:499px;top:2013px}
.contact-info{left:499px;top:2070px;font-size:14px;line-height:29px;color:var(--ink);list-style:none}
.contact-info li{display:flex;align-items:center;gap:14px}
.contact-info svg{width:14px;height:14px;fill:var(--teal)}
.field{background:#fff;border:1px solid #d4d4d4;font-size:13px;color:var(--ink);padding:10px 12px;height:39px}
.f1{left:499px;top:2172px;width:267px}
.f2{left:499px;top:2227px;width:267px}
.f3{left:499px;top:2279px;width:267px}
.f4{left:783px;top:2172px;width:267px;height:94px}
.submit{left:783px;top:2279px;width:267px;height:39px;line-height:39px;font-size:14px}
/* partners */
.partners-title{left:0;top:2430px;width:1200px;text-align:center}
.badge{top:2499px;height:100px;background:#d9dde0}
.b1{left:166px;width:181px}.b2{left:399px;width:117px}.b3{left:579px;width:191px}.b4{left:818px;width:214px}
/* footer */
.site-footer{left:0;top:2655px;width:1200px;height:267px;background:var(--footer)}
.site-footer .brand{position:absolute;left:74px;top:2729px}
.copy{left:74px;top:2817px;font-size:12px;line-height:23px;color:var(--text)}
.fcol{top:2694px;font-size:13.5px;line-height:28px;color:var(--ink);list-style:none}
.fcol .head{font-weight:900;font-size:14px;text-transform:uppercase}
.fc1{left:434px}.fc2{left:625px}.fc3{left:894px}
.social{display:flex;gap:20px;margin-top:8px}
.social span{width:18px;height:18px;border-radius:50%;background:var(--navy)}
</style>
</head>
<body>

<header class="abs site-header">
  <div class="brand"><span class="brand-dot"></span><span class="brand-name">NEXOL</span></div>
  <nav class="main-nav">
    <a class="active">HOME</a>
    <a style="margin-left:22px">ABOUT US</a>
    <a style="margin-left:33px">OUR SOLUTIONS</a>
    <a style="margin-left:33px">OUR TEAM</a>
    <a style="margin-left:33px">JOB</a>
    <a style="margin-left:33px">CONTACT US</a>
  </nav>
</header>

<section class="abs hero" role="img" aria-label="City skyline at night with light trails on a highway">
  <h1>We Build Mission Critical<br>Environments</h1>
  <div class="hero-dots"><span></span><span></span><span></span><span></span></div>
</section>

<div class="abs about-photo" role="img" aria-label="Hand touching a glowing digital network"></div>
<section class="abs about-text">
  <h2 class="section-title">About<span class="sub">Nexol Critical IT System</span></h2>
  <p>Lorem ipsum dolor sit amet, consectetur adipisicing elit, sed do eiusmod tempor incididunt ut labore et doloreasdes magna aliqua. Ut enim ad minim veniam, quis nostrud exercitation ullamco laboris nisi ut aliquip ex ea commodalo consequat. Duis aute irure dolor in reprehenderit in voluptate velit esse cillum dolore eu fugiat nulla pariatur. Excepteur sint occaecat cupidatat non proident, sunt in culpa qui officia deserunt mollit anim id est laborum.</p>
  <span class="btn btn-grad">Read More</span>
</section>

<div class="abs services-band" role="img" aria-label="Dark technology background"></div>
<h2 class="abs services-title">WHAT WE DO</h2>

<article class="abs card c1">
  <svg viewBox="0 0 64 64" fill="none" stroke="#fff" stroke-width="2"><circle cx="24" cy="36" r="12"/><circle cx="24" cy="36" r="5"/><circle cx="44" cy="20" r="8"/><circle cx="44" cy="20" r="3"/></svg>
  <h3>Automation<br>&amp; Deployment</h3>
  <p>We take care of the complete Design and implementation of Automation and Deployment within your organization.</p>
</article>
<article class="abs card c2">
  <svg viewBox="0 0 64 64" fill="none" stroke="#fff" stroke-width="2"><path d="M20 44 L44 14 Q52 10 50 20 L22 48 Z"/><path d="M22 36 L12 38 L20 30"/><path d="M28 42 L26 52 L34 44"/></svg>
  <h3>Mission Critical<br>Solutions</h3>
  <p>Nexol builds High-end solutions that must be available 24/7. We do this in cooperation with our partners.</p>
</article>
<article class="abs card c3">
  <svg viewBox="0 0 64 64" fill="none" stroke="#fff" stroke-width="2"><path d="M18 44 H46 A9 9 0 0 0 46 26 A13 13 0 0 0 22 24 A10 10 0 0 0 18 44 Z"/></svg>
  <h3>Cloud Consultancy</h3>
  <p>Our consultants ensure a flawless implementation and migration of your infrastructure to the public, private and / or hybrid cloud.</p>
</article>
<article class="abs card c4">
  <svg viewBox="0 0 64 64" fill="none" stroke="#fff" stroke-width="2"><rect x="26" y="10" width="12" height="10"/><rect x="10" y="40" width="12" height="10"/><rect x="26" y="40" width="12" height="10"/><rect x="42" y="40" width="12" height="10"/><path d="M32 20 V30 M16 40 V30 H48 V40 M32 30 V40"/></svg>
  <h3>Hyperconverged<br>Infrastructures</h3>
  <p>Nexol supplies Hyperconverged Solutions where compute and / or storage is fully integrated and where you create...</p>
</article>

<h2 class="abs section-title jobs-title">Jobs <em>Openings</em></h2>
<article class="abs job job-a">
  <div class="job-mark"></div>
  <h4>Kernix Engineer</h4>
  <p>You will work in a team with Kernix engineers from Nexol BV This team is used by our large customers. You will have an independent position with nice clients.</p>
  <span class="btn">More Info</span>
</article>
<article class="abs job job-b">
  <div class="job-mark"></div>
  <h4>Windara Engineer</h4>
  <p>You will work in a team with Windara engineers from Nexol BV This team is used by our large customers. You will have an independent position with nice clients.</p>
  <span class="btn">More Info</span>
</article>
<div class="abs jobs-photo" role="img" aria-label="Business people shaking hands in an office"></div>

<section class="abs contact"></section>
<div class="abs contact-photo" role="img" aria-label="Businessman in a suit working at a laptop"></div>
<h2 class="abs section-title contact-title">Quick <em>Contact</em></h2>
<ul class="abs contact-info">
  <li><svg viewBox="0 0 14 14"><path d="M7 0A5 5 0 0 0 2 5c0 4 5 9 5 9s5-5 5-9A5 5 0 0 0 7 0zm0 7a2 2 0 1 1 0-4 2 2 0 0 1 0 4z"/></svg>Lindenhof 14, 3512 KT Utrecht</li>
  <li><svg viewBox="0 0 14 14"><path d="M3 0l3 3-2 2c1 2 3 4 5 5l2-2 3 3-2 3C6 14 0 8 0 2z"/></svg>030-5551274</li>
  <li><svg viewBox="0 0 14 14"><path d="M0 2h14v10H0z M0 2l7 6 7-6" /></svg>info@nexol.nl</li>
</ul>
<div class="abs field f1">Name</div>
<div class="abs field f2">Phone No</div>
<div class="abs field f3">Email Address</div>
<div class="abs field f4">Message</div>
<span class="abs btn btn-grad submit">Submit</span>

<h2 class="abs section-title partners-title">Our <em>Partners</em></h2>
<div class="abs badge b1"></div>
<div class="abs badge b2"></div>
<div class="abs badge b3"></div>
<div class="abs badge b4"></div>

<footer class="abs site-footer"></footer>
<div class="abs" style="left:74px;top:2729px"><div class="brand"><span class="brand-dot"></span><span class="brand-name">NEXOL</span></div></div>
<p class="abs copy">Copyright © 2018 Company Name<br>All Right Reserved</p>
<ul class="abs fcol fc1">
  <li class="head">Solutions</li><li>Home</li><li>About Us</li><li>Our Solutions</li><li>Our Team</li><li>Job</li><li>Contact Us</li>
</ul>
<ul class="abs fcol fc2">
  <li class="head">Solutions</li><li>Automation &amp; Deployment</li><li>Mission Critical Solutions</li><li>Cloud Consultancy</li><li>Hyperconverged Infrastructures</li>
</ul>
<div class="abs fcol fc3">
  <div class="head">Follow Us</div>
  <div class="social"><span></span><span></span><span></span><span></span><span></span></div>
</div>

</body>
</html>
```